Non fiction leadership Book Cover design needed for “Stay Bold: Build On Lasting Discipline”

I need a front cover design for a new book 6 X 9 traditional non-fiction book.

Title: "Stay BOLD - Build On Lasting Discipline"

The subtitle is not finalized- so use 2 lines of smaller dummy text

My brand guide is attached (please use the tan color sparingly)

I'd like to see BOLD look like it is in motion and "flying" across the page

Need CREATIVE designs and options

Do not want my picture on the front cover - I do want it on the back cover.

On the front cover I’d like to see creative use of font to create movement on “BOLD”

Target Market(s)

Business leaders

Industry/Entity Type

Aviation

Font styles to use
Other font styles liked:
• See style guide- can add additional font (modern script or san serif)

Colors
0054AA
0677BA
7BADD7
CADEEF
E8F1F8
EB3D1F
EC4F4E
F09395
F8D3D4
FCEDEE

Requirements
Must have
• Creative font use, using perspective to create movement/motion on BOLD
Should not have
• My picture on the front cover- my picture should be on the back cover

```html
<!DOCTYPE html>
<html lang="en">
<head>
<meta charset="utf-8">
<title>Stay Bold: Build On Lasting Discipline — Front Cover</title>
<link rel="stylesheet" href="https://fonts.googleapis.com/css2?family=Bebas+Neue&family=Montserrat:wght@400;500;600&display=swap">
<style>
  :root {
    --stage-grey: #b1b0ac;
    --cover-red: #ee2732;
    --cover-paper: #e8e7e7;
    --title-navy: #04041c;
    --spark-gold: #7a5e32;
    --text-light: #f4f1f1;
  }
  * { margin: 0; padding: 0; box-sizing: border-box; }
  html, body {
    width: 1200px;
    height: 960px;
    overflow: hidden;
    background: var(--stage-grey);
  }
  .canvas {
    position: relative;
    width: 1200px;
    height: 960px;
  }
  .book-cover {
    position: absolute;
    left: 310px;
    top: 40px;
    width: 580px;
    height: 880px;
    background: var(--cover-paper);
    overflow: hidden;
  }
  .arch-band {
    position: absolute;
    left: 0;
    top: 0;
    width: 580px;
    height: 360px;
  }
  .arch-band path,
  .arch-band rect,
  .arch-band circle { fill: var(--cover-red); }
  .subtitle-dummy {
    position: absolute;
    top: 34px;
    left: 0;
    width: 100%;
    text-align: center;
    font-family: "Montserrat", sans-serif;
    font-weight: 500;
    font-size: 11.5px;
    line-height: 16px;
    color: var(--text-light);
  }
  .aircraft-emblem {
    position: absolute;
    left: 238px;
    top: 82px;
    width: 104px;
    height: 132px;
    background: linear-gradient(180deg, #f1e9e9 0%, #f6d2d4 100%);
    border-radius: 6px;
    opacity: 0.9;
  }
  .title-lead {
    position: absolute;
    top: 300px;
    left: 0;
    width: 100%;
    text-align: center;
    font-family: "Bebas Neue", sans-serif;
    font-size: 112px;
    line-height: 1;
    color: var(--cover-red);
    letter-spacing: 1px;
  }
  .title-main {
    position: absolute;
    top: 388px;
    left: 0;
    width: 100%;
    text-align: center;
    perspective: 600px;
  }
  .title-main span {
    display: inline-block;
    font-family: "Bebas Neue", sans-serif;
    font-size: 272px;
    line-height: 0.8;
    letter-spacing: 2px;
    background: linear-gradient(180deg, var(--title-navy) 0%, var(--title-navy) 62%, #1d1a22 80%, var(--spark-gold) 100%);
    -webkit-background-clip: text;
    background-clip: text;
    color: transparent;
    transform: scaleY(1.45) rotateY(-12deg);
    transform-origin: center top;
  }
  .tagline-bar {
    position: absolute;
    top: 727px;
    left: 109px;
    width: 362px;
    height: 39px;
    background: var(--cover-red);
    display: flex;
    align-items: center;
    justify-content: center;
    font-family: "Montserrat", sans-serif;
    font-weight: 500;
    font-size: 17px;
    letter-spacing: 0.6px;
    color: var(--text-light);
    white-space: nowrap;
  }
  .author-name {
    position: absolute;
    top: 808px;
    left: 0;
    width: 100%;
    text-align: center;
    font-family: "Montserrat", sans-serif;
    font-weight: 600;
    font-size: 31px;
    color: var(--cover-red);
  }
</style>
</head>
<body>
<main class="canvas">
  <section class="book-cover">
    <svg class="arch-band" viewBox="0 0 580 360" aria-hidden="true">
      <rect x="0" y="0" width="580" height="214"/>
      <circle cx="121" cy="161" r="177"/>
      <circle cx="459" cy="161" r="177"/>
    </svg>

    <p class="subtitle-dummy">Lorem ipsum dolor sit amet, consectetuer adipiscing<br>sed diam nonummy nibh euismod tincidunt</p>

    <div class="aircraft-emblem" role="img" aria-label="White silhouette of a helicopter seen from above, rotor blades crossed"></div>

    <h1 class="title-lead">STAY</h1>
    <div class="title-main"><span>BOLD</span></div>

    <p class="tagline-bar">BUILD ON LASTING DISCIPLINE</p>

    <p class="author-name">Margaret Holloway</p>
  </section>
</main>
</body>
</html>
```